Plakat für Hausverwaltung
Zielgruppe
Hausverwaltung
(Verwaltung von Wohn- und Gewerbeimmobilien)
Aufgabenstellung
Es soll ein Werbeplakat werden, Die Inhalte der Dienstleistung und die Firmenfarben kann der Webseite entnommen werden.
Ein guter Werbespruch und ansprechendes Desing ohne viel Schrift.

```html
<!DOCTYPE html>
<html lang="de">
<head>
<meta charset="utf-8">
<title>KLW Hausverwaltung Plakat</title>
<link rel="stylesheet" href="https://fonts.googleapis.com/css2?family=Montserrat:wght@300;400;500&family=Poppins:wght@900&display=swap">
<style>
  :root {
    --sand: #cdc5c0;
    --sand-light: #ddd7d3;
    --ink: #000000;
    --paper: #ffffff;
    --muted: #3a3a3a;
    --photo-a: #c9c4bc;
    --photo-b: #7d7a77;
  }
  * { margin: 0; padding: 0; box-sizing: border-box; }
  html, body { width: 920px; height: 1200px; overflow: hidden; background: var(--paper); }
  .poster { position: relative; width: 920px; height: 1200px; background: var(--ink); font-family: "Montserrat", sans-serif; color: var(--paper); }

  .topbar { position: absolute; left: 0; top: 0; width: 920px; height: 89px; background: var(--sand); }
  .brand { position: absolute; left: 42px; top: 18px; width: 310px; text-align: center; color: var(--muted); }
  .brand-name { font-size: 26px; font-weight: 400; letter-spacing: 8px; line-height: 28px; }
  .brand-tag { font-size: 14px; font-weight: 400; margin-top: 6px; }
  .skyline { position: absolute; left: 365px; top: 10px; width: 555px; height: 68px; background: linear-gradient(180deg, var(--sand), var(--sand-light)); }

  .headline { position: absolute; left: 56px; top: 168px; font-family: "Poppins", sans-serif; font-weight: 900; font-size: 90px; line-height: 110px; letter-spacing: 0; transform: skewY(-5deg); transform-origin: left top; }
  .headline span { display: block; }

  .claim { position: absolute; left: 56px; top: 658px; width: 760px; transform: skewY(-4.8deg); transform-origin: left top; }
  .claim-line { height: 63px; border-top: 1px solid var(--paper); font-size: 40px; font-weight: 400; line-height: 63px; letter-spacing: 1px; padding-top: 6px; white-space: nowrap; }
  .claim-line:last-child { height: 0; }

  .services { position: absolute; left: 62px; top: 912px; list-style: none; }
  .services li { display: flex; align-items: center; height: 36px; font-size: 16px; font-weight: 300; letter-spacing: .5px; }
  .services svg { width: 16px; height: 16px; margin-right: 30px; }

  .team-photo { position: absolute; left: 340px; top: 870px; width: 580px; height: 223px; background: linear-gradient(180deg, var(--photo-a), var(--photo-b)); }

  .footer { position: absolute; left: 0; top: 1093px; width: 920px; height: 107px; background: var(--sand); color: var(--ink); }
  .footer-title { position: absolute; left: 196px; top: 22px; font-size: 24px; font-weight: 400; }
  .contact { position: absolute; top: 20px; font-size: 9px; line-height: 11px; color: var(--muted); }
  .contact svg { display: block; margin-bottom: 8px; }
  .contact-address { left: 340px; }
  .contact-mail { left: 490px; top: 26px; }
  .contact-phone { left: 637px; }
</style>
</head>
<body>
<main class="poster">
  <header class="topbar">
    <div class="brand">
      <div class="brand-name">KLW</div>
      <div class="brand-tag">Haus- und Grundstücksverwaltungs GmbH</div>
    </div>
    <div class="skyline" role="img" aria-label="Linienzeichnung einer Häuserzeile"></div>
  </header>

  <h1 class="headline">
    <span>Belastet Sie</span>
    <span>Verwaltung</span>
    <span>Ihrer</span>
    <span>Immobilie?</span>
  </h1>

  <div class="claim">
    <div class="claim-line">Diese Aufgabe können wir</div>
    <div class="claim-line">für Sie übernehmen. Profesionell,</div>
    <div class="claim-line">reibungslos, zuverlässig.</div>
    <div class="claim-line"></div>
  </div>

  <ul class="services">
    <li><svg viewBox="0 0 16 16"><path d="M1 7 L8 1 L15 7 V15 H1 Z" fill="#ffffff"/></svg>Wohnungsverwaltung</li>
    <li><svg viewBox="0 0 16 16"><path d="M1 7 L8 1 L15 7 V15 H1 Z" fill="#ffffff"/></svg>Sondereigentum</li>
    <li><svg viewBox="0 0 16 16"><path d="M1 7 L8 1 L15 7 V15 H1 Z" fill="#ffffff"/></svg>Mietverwaltung</li>
  </ul>

  <div class="team-photo" role="img" aria-label="Foto des dreiköpfigen Teams vor einem Regal mit Aktenordnern"></div>

  <footer class="footer">
    <div class="footer-title">Kontakt</div>
    <div class="contact contact-address">
      <svg width="24" height="24" viewBox="0 0 24 24" fill="none" stroke="#222" stroke-width="1.3"><path d="M2 11 L12 2 L22 11 V22 H2 Z"/></svg>
      Lindenhofer Allee 12<br>35041 Talburg
    </div>
    <div class="contact contact-mail">
      <svg width="26" height="16" viewBox="0 0 26 16" fill="none" stroke="#222" stroke-width="1.3"><rect x="1" y="1" width="24" height="14"/><polyline points="1,1 13,10 25,1"/></svg>
      info@klw-talburg.de
    </div>
    <div class="contact contact-phone">
      <svg width="16" height="26" viewBox="0 0 16 26" fill="none" stroke="#222" stroke-width="1.3"><rect x="1" y="1" width="14" height="24" rx="2"/><line x1="1" y1="20" x2="15" y2="20"/></svg>
      06431 582930
    </div>
  </footer>
</main>
</body>
</html>
```